Business Card for my New Brokerage

Looking to get a business card design for my new Real Estate Brokerage.
I want it with Picture, Phone Number, Email, Website, Office Address
Name and Designation. Please add logo too.

Target Market(s)

Real Estate Investors or Home Buyers

Industry/Entity Type

Real Estate

Contact Information for Business Card

Name, Email, Phone Number, website, email, office address

Colors
EB3D1F
EC4F4E
F09395
F8D3D4
FCEDEE

Requirements
Must have
• Minimalistic, Clean, Modern, Photo
Nice to have
• White and Red Colors

```html
<!DOCTYPE html>
<html lang="en">
<head>
<meta charset="UTF-8">
<title>Ember Realty Inc – Business Card</title>
<link href="https://fonts.googleapis.com/css2?family=Montserrat:wght@400;500;700&display=swap" rel="stylesheet">
<style>
  :root {
    --red: #e00000;
    --red-deep: #c40000;
    --white: #ffffff;
    --ink: #3a3a3a;
    --silver: #bdbdbd;
    --stage: #ececec;
    --photo-a: #e8e4df;
    --photo-b: #9aa3b3;
  }
  * { margin: 0; padding: 0; box-sizing: border-box; }
  html, body {
    width: 1200px; height: 786px; overflow: hidden;
    background: var(--stage);
    font-family: "Montserrat", Arial, sans-serif;
  }
  .stage {
    width: 1200px; height: 786px;
    display: flex; align-items: center; justify-content: center; gap: 40px;
  }
  .card {
    width: 540px; height: 309px; position: relative;
    box-shadow: 0 10px 28px rgba(0,0,0,0.18);
  }
  /* Front */
  .card-front {
    background: var(--white);
    border: 6px solid var(--red);
    display: flex; align-items: center;
  }
  .portrait {
    width: 138px; height: 138px; border-radius: 50%;
    border: 2px solid var(--red);
    background: radial-gradient(circle at 45% 40%, var(--photo-a) 0%, var(--photo-b) 100%);
    margin-left: 92px; flex-shrink: 0;
  }
  .divider {
    width: 1px; height: 150px; background: var(--red);
    opacity: 0.6; margin: 0 26px 0 34px; flex-shrink: 0;
  }
  .details { color: var(--ink); }
  .name {
    color: var(--red); font-weight: 700; font-size: 19px;
    letter-spacing: 0.5px; line-height: 1.1;
  }
  .title { font-size: 12px; margin-top: 3px; }
  .address { font-size: 12px; line-height: 1.4; margin-top: 12px; }
  .contacts { list-style: none; margin-top: 10px; font-size: 12px; line-height: 1.45; }
  .contacts li { display: flex; align-items: center; gap: 6px; }
  .contacts svg { width: 9px; height: 9px; fill: none; stroke: var(--red); stroke-width: 2; flex-shrink: 0; }
  /* Back */
  .card-back {
    background: var(--red);
    display: flex; align-items: center; justify-content: center;
  }
  .brand {
    color: var(--silver); font-weight: 700; text-align: center;
    display: flex; align-items: center; gap: 10px;
  }
  .brand-mark {
    width: 14px; height: 14px; border-radius: 50%; background: var(--silver);
  }
  .brand-name { font-size: 40px; letter-spacing: 3px; line-height: 1; }
  .brand-sub { display: block; font-size: 14px; letter-spacing: 6px; margin-top: 8px; }
</style>
</head>
<body>
<main class="stage">
  <section class="card card-front" aria-label="Business card front">
    <div class="portrait" role="img" aria-label="Portrait photo of the broker"></div>
    <div class="divider"></div>
    <div class="details">
      <h1 class="name">DANIEL REYES</h1>
      <p class="title">Founder and President</p>
      <p class="address">1870 Maple Ridge Way<br>Fairview, GA 30000</p>
      <ul class="contacts">
        <li>
          <svg viewBox="0 0 10 10" aria-hidden="true"><path d="M2 1 L4 3 L3 4 Q4 6 6 7 L7 6 L9 8 L8 9 Q3 9 1 2 Z"/></svg>
          +330 5120-4700
        </li>
        <li>
          <svg viewBox="0 0 10 10" aria-hidden="true"><rect x="1" y="2" width="8" height="6"/><path d="M1 2 L5 5.5 L9 2"/></svg>
          info@emberrealtyinc.com
        </li>
        <li>
          <svg viewBox="0 0 10 10" aria-hidden="true"><circle cx="5" cy="5" r="4"/><path d="M1 5 H9 M5 1 Q2.5 5 5 9 M5 1 Q7.5 5 5 9"/></svg>
          www.emberrealtyinc.com
        </li>
      </ul>
    </div>
  </section>

  <section class="card card-back" aria-label="Business card back">
    <div class="brand">
      <span class="brand-mark" aria-hidden="true"></span>
      <div>
        <span class="brand-name">EMBER</span>
        <span class="brand-sub">REALTY INC</span>
      </div>
    </div>
  </section>
</main>
</body>
</html>
```